Kelumo.cn needs pages to be re-designed

www.kelumo.cn is our current new site which was launched in April.
We're a financial services website in the crowdfunding space in China to connect borrower's and lender's.

test.kelumo.cn is our test site
u: test
p: newtest
http://test.kelumo.cn/
http://test.kelumo.cn/user/accounts/new_lender
http://test.kelumo.cn/user/accounts/new_borrower
http://test.kelumo.cn/introductions/protection
http://test.kelumo.cn/introductions
http://test.kelumo.cn/introductions/kelumo_admin
http://test.kelumo.cn/introductions/contact
Some of the pages have pop-ups in the bloc's of the pages. Please click the links, to see more content.

User's currently criticize the website for being:
- Too Western looking
- Too simple, too little content
- Content NOT in the pop-ups are too simple
- Pictures are too big and too much blank space
- Relevant information is not there when needed
- The pictures are too generic

What we would like to do is re-design those pages with the same color scheme and style to be more compelling, efficient, non-intimidating and easy-to-use. Our audience is Ages 25-35 predominantly male investors.
We are looking for more ideas to make the content match the style, while bridging western and chinese design. Our ultimate goal is to increase registrants to the website and highlight our core competitive advantages.

Some competitors websites are:
www.fobuxiqi.com
www.tamev.com
www.zzzlendo.com

Reason: Not enough good designs that follow the prompt. Same style, better information layout!

Reason: Still have not received a design we're satisfied with

Reason: WE DONT WANT A COMPLETE REDESIGN OF PAGES . KEEP THE EXACT SAME COLOR AND STYLE - WE WANT CONTENT RE-DESIGN! THE BLOCS ARE TOO SIMPLE - WE WANT MORE CONTENT INSIDE.

Reason: no new designs

Reason: no new designs

Reason: other non-registered pages need to be re-designed

```html
<!DOCTYPE html>
<html lang="zh-CN">
<head>
<meta charset="utf-8">
<title>可路贷 Kelumo.cn</title>
<link href="https://fonts.googleapis.com/css2?family=Noto+Sans+SC:wght@400;500;700&family=Roboto:wght@400;500;700&display=swap" rel="stylesheet">
<style>
:root{
  --green:#3cb52a;
  --green-light:#6ad24a;
  --green-text:#4aa52a;
  --blue:#2f8fd0;
  --blue-btn:#1e86c5;
  --ink:#333;
  --ink-soft:#666;
  --ink-faint:#999;
  --line:#e3e3e3;
  --bg-soft:#f2f4f5;
  --topbar:#3b3d40;
  --footer:#2c2e33;
  --footer-deep:#25272b;
  --orange:#f7923a;
  --yellow:#f5b324;
  --red:#ef6b6f;
  --purple:#9a7a9f;
}
*{margin:0;padding:0;box-sizing:border-box}
html,body{width:1200px;height:2361px;overflow:hidden}
body{font-family:"Noto Sans SC","Roboto",sans-serif;color:var(--ink);background:#fff;font-size:13px;position:relative}
.wrap{width:924px;margin:0 auto;position:relative}
a{color:inherit;text-decoration:none}

/* top bar */
.topbar{height:34px;background:var(--topbar);color:#ddd;font-size:12px}
.topbar .wrap{display:flex;align-items:center;height:34px;gap:18px}
.topbar .right{margin-left:auto;display:flex;gap:18px;align-items:center}
.topbar .login{color:var(--green-light)}
.lang{width:40px;height:18px;border:1px solid #666;border-radius:2px;font-size:10px;display:flex;align-items:center;justify-content:center}

/* header */
.header{height:86px;background:#fff;border-bottom:1px solid var(--line)}
.header .wrap{display:flex;align-items:center;height:86px}
.brand{display:flex;align-items:center;gap:10px}
.brand .dot{width:42px;height:42px;border-radius:50%;background:var(--green)}
.brand .name{font-size:22px;font-weight:500;line-height:1}
.brand .name small{display:block;font-size:11px;color:var(--ink-faint);margin-top:4px}
.nav{margin-left:auto;display:flex;gap:58px;font-size:17px;color:#444}

/* hero */
.hero{height:335px;position:relative;background:linear-gradient(90deg,#6a6a70 0%,#c9ccd0 28%,#e8eaec 55%,#cfd2d6 80%,#9fa3a8 100%);overflow:hidden}
.hero .copy{position:absolute;left:656px;top:72px;width:440px}
.hero h1{font-size:31px;font-weight:700;line-height:1.35;color:#222;letter-spacing:3px}
.hero p{margin-top:14px;font-size:14px;line-height:1.75;color:#333;font-weight:500}

/* promo strip */
.strip{height:125px;background:var(--bg-soft)}
.strip .wrap{display:flex;align-items:center;height:125px}
.strip .slogan{font-size:21px;color:var(--green-text);line-height:1.6;letter-spacing:2px}
.strip .notice{margin-left:auto;text-align:right;margin-right:22px}
.strip .notice b{font-size:22px;font-weight:500}
.strip .notice span{display:block;font-size:12px;color:var(--ink-faint);margin-top:2px}
.btn-green{display:inline-flex;align-items:center;gap:8px;background:linear-gradient(#6ad24a,#35a726);color:#fff;border-radius:20px;font-size:16px;padding:0 20px;height:40px}
.btn-green svg{width:14px;height:14px}

/* features */
.features{padding:54px 0 40px}
.features .wrap{display:flex;gap:56px}
.feature{flex:1}
.feature h3{display:flex;align-items:center;gap:34px;font-size:19px;font-weight:500}
.feature h3 svg{width:26px;height:26px}
.feature .lead{margin-top:14px;font-size:13px;color:var(--ink-soft)}
.feature .body{margin-top:10px;font-size:12px;color:var(--ink-faint);line-height:1.9}
.feature .more{margin-top:10px;font-size:11px;color:var(--green-text)}

/* ticker */
.ticker{height:42px;border-top:1px solid var(--line);border-bottom:1px solid var(--line);background:#fafafa;margin-top:10px}
.ticker .wrap{display:flex;align-items:center;justify-content:center;height:42px;gap:40px;font-size:20px;font-weight:700}
.ticker .b{color:var(--blue)}
.ticker .g{color:var(--green)}
.ticker .arr{position:absolute;top:12px;width:12px;height:18px}

/* loan table */
.loans{margin-top:80px}
.card{border:1px solid #d8d8d8;box-shadow:0 2px 6px rgba(0,0,0,.08);background:#fff}
.loans table{width:100%;border-collapse:collapse}
.loans th{height:46px;background:linear-gradient(#fafafa,#ececec);text-align:left;font-size:16px;font-weight:500;color:#222;padding-left:24px}
.loans td{height:55px;border-top:1px solid #eee;font-size:13px;color:var(--ink-soft);padding-left:24px}
.loans tr.hl td{background:#f3f3f3}
.loans td.title{font-size:11px;color:#555}
.badges{display:flex;gap:4px}
.badge{width:18px;height:18px;border-radius:50%;color:#fff;font-size:10px;font-weight:700;display:flex;align-items:center;justify-content:center;background:var(--green)}
.badge.b{background:#59a3dd}
.bar{display:flex;align-items:center;gap:14px;font-size:11px}
.bar i{display:block;width:64px;height:8px;background:#ddd;border-radius:4px;overflow:hidden}
.bar i b{display:block;height:100%;background:var(--green)}
.pill{display:inline-block;width:62px;height:20px;border-radius:10px;font-size:10px;text-align:center;line-height:20px;color:#fff;background:var(--blue-btn)}
.pill.off{background:#c9c9c9}

/* stats */
.stats{margin-top:28px}
.stats .wrap{display:flex;align-items:center;height:96px}
.stat{padding-right:40px;margin-right:40px;border-right:1px solid var(--line)}
.stat b{font-size:21px;font-weight:500;display:block}
.stat span{font-size:11px;color:var(--ink-faint)}
.stat.last{border:0}
.stats .btn-green{margin-left:auto}

/* products */
.section-title{font-size:21px;font-weight:500;margin-top:40px}
.products{display:flex;margin-top:16px;height:192px}
.product{flex:1;color:#fff;padding:26px 24px}
.product .k{font-size:14px}
.product .rate{font-size:27px;font-weight:700;margin-top:10px;font-family:"Roboto",sans-serif}
.product .d{font-size:13px;margin-top:8px}
.product .btn-green{margin-top:14px;height:38px;font-size:16px;padding:0 22px}
.orange{background:var(--orange)}.yellow{background:var(--yellow)}.red{background:var(--red)}.purple{background:var(--purple)}

/* partners */
.partners{text-align:center;margin-top:56px}
.partners h2{font-size:24px;font-weight:500;letter-spacing:2px}
.banks{display:grid;grid-template-columns:repeat(6,1fr);gap:16px 10px;width:660px;margin:28px auto 0}
.bank{display:flex;align-items:center;gap:6px;font-size:13px;color:#444;justify-content:center}
.bank i{width:12px;height:12px;border-radius:50%;background:#c9302c}
.bank.bl i{background:#2a6db5}
.bank.gr i{background:#2a9a5a}
.partners .arr{position:absolute;top:50px;width:16px;height:28px}

.allies{margin-top:56px;height:70px;background:#ececec;border-top:1px solid #ddd}
.allies .wrap{display:flex;align-items:center;justify-content:space-between;height:70px;font-size:15px;color:#333}
.ally{display:flex;align-items:center;gap:8px}
.ally i{width:14px;height:14px;background:#2f5fa8}
.ally.r i{background:#c0242b;border-radius:50%}

/* footer */
.footer{background:var(--footer);color:#ccc;height:268px;position:absolute;left:0;right:0;top:2093px}
.footer .wrap{display:flex;padding-top:38px}
.links{display:grid;grid-template-columns:auto auto;column-gap:60px;row-gap:9px;font-size:12px;width:400px}
.links.r{width:auto;grid-template-columns:auto}
.certs{margin-left:20px;width:236px;height:126px;background:#1f2125;border-radius:3px;display:grid;grid-template-columns:1fr 1fr;gap:8px;padding:10px}
.certs i{background:#d9d9d9;border-radius:2px}
.contact{margin-left:auto;width:196px}
.social{display:flex;gap:14px}
.social i{width:30px;height:30px;border-radius:4px;background:#4a4d52}
.contact .t{font-size:12px;color:var(--green-light);margin-top:10px}
.contact .ph{font-size:22px;font-weight:700;color:#fff;margin-top:10px;font-family:"Roboto",sans-serif}
.contact .s{font-size:11px;color:#999;margin-top:6px;line-height:1.6}
.footer .bottom{position:absolute;left:0;right:0;bottom:0;height:52px;background:var(--footer-deep);font-size:11px;color:#777}
.footer .bottom .wrap{padding-top:18px;gap:40px}
</style>
</head>
<body>

<div class="topbar">
  <div class="wrap">
    <span>☎ 400 - 820 - 5577</span>
    <span>✉ 专业网络借贷平台 为您的资金保驾护航</span>
    <div class="right">
      <a class="login" href="#">登录 | 注册</a>
      <a href="#">我的账户 · 帮助中心</a>
      <span class="lang">EN ▾</span>
    </div>
  </div>
</div>

<header class="header">
  <div class="wrap">
    <div class="brand">
      <span class="dot"></span>
      <div class="name">可路贷<small>kelumo.cn</small></div>
    </div>
    <nav class="nav">
      <a href="#">我要投资理财</a>
      <a href="#">我要借款融资</a>
      <a href="#">安全保障中心</a>
    </nav>
  </div>
</header>

<section class="hero" role="img" aria-label="商务人士在明亮办公室中的照片，左侧为一位微笑的职业女性">
  <div class="copy">
    <h1>把握每一次投资<br>稳健收益 安心理财</h1>
    <p>风险保障金全额垫付，资金第三方托管<br>本息保障，灵活期限，收益透明可查<br>随时随地，轻松开启您的财富之路</p>
  </div>
</section>

<section class="strip">
  <div class="wrap">
    <div class="slogan">借 · 投资更简单<br>透明 · 稳健 · 有保障</div>
    <div class="notice"><b>新手注册，立享专属福利</b><span>2014-07-17</span></div>
    <a class="btn-green" href="#">立即注册 <svg viewBox="0 0 14 14"><path d="M2 3h6V0l6 7-6 7v-3H2z" fill="#fff"/></svg></a>
  </div>
</section>

<section class="features">
  <div class="wrap">
    <div class="feature">
      <h3><svg viewBox="0 0 26 26"><rect x="2" y="14" width="5" height="10" fill="#f29b2c"/><rect x="9" y="8" width="5" height="16" fill="#3cb52a"/><rect x="16" y="3" width="5" height="21" fill="#2f8fd0"/></svg>收益</h3>
      <p class="lead">年化收益最高可达15%，远超银行</p>
      <p class="body">投资门槛低，百元起投，收益按月到账，资金灵活安排，<br>多种期限产品自由选择，收益清晰可查。</p>
      <p class="more">了解更多 &gt;&gt;</p>
    </div>
    <div class="feature">
      <h3><svg viewBox="0 0 26 26"><rect x="5" y="11" width="16" height="13" rx="2" fill="#888"/><path d="M8 11V7a5 5 0 0 1 10 0v4" stroke="#888" stroke-width="2.5" fill="none"/></svg>安全</h3>
      <p class="lead">风险保障金 本息全额保障</p>
      <p class="body">资金第三方托管，严格风控审核流程，<br>逾期自动垫付本息，多重保障。</p>
      <p class="more">了解更多 &gt;&gt;</p>
    </div>
    <div class="feature">
      <h3><svg viewBox="0 0 26 26"><circle cx="13" cy="13" r="10" fill="none" stroke="#888" stroke-width="2"/><circle cx="13" cy="13" r="4" fill="#888"/></svg>便捷</h3>
      <p class="lead">在线操作，一键投资</p>
      <p class="body">注册即可投资，流程简单，<br>随时查看收益，<br>提现快速到账。</p>
      <p class="more">了解更多 &gt;&gt;</p>
    </div>
  </div>
</section>

<div class="ticker">
  <div class="wrap">
    <svg class="arr" style="left:0" viewBox="0 0 12 18"><path d="M10 2 3 9l7 7" stroke="#bbb" stroke-width="2" fill="none"/></svg>
    <span class="b">最新投资 50000元 年利率15.0%</span>
    <span class="g">新手标 130元 年利率15.0%</span>
    <svg class="arr" style="right:0" viewBox="0 0 12 18"><path d="M2 2l7 7-7 7" stroke="#bbb" stroke-width="2" fill="none"/></svg>
  </div>
</div>

<section class="loans wrap">
  <div class="card">
    <table>
      <tr><th>借款标题</th><th>信用等级</th><th>年利率</th><th>借款金额</th><th>期限</th><th>进度</th><th></th></tr>
      <tr><td class="title">经营周转借款 用于扩大门店规模经营</td><td><div class="badges"><span class="badge">A</span><span class="badge">保</span></div></td><td>15.0%</td><td>50,000 元</td><td>12 个月</td><td><div class="bar"><i><b style="width:7%"></b></i>6.69%</div></td><td><span class="pill">投标</span></td></tr>
      <tr><td class="title">经营周转借款 用于采购原材料及货物</td><td><div class="badges"><span class="badge">A</span><span class="badge">保</span><span class="badge b">新</span></div></td><td>15.0%</td><td>8197.0 元</td><td>6 个月</td><td><div class="bar"><i><b style="width:9%"></b></i>9.23%</div></td><td><span class="pill">投标</span></td></tr>
      <tr class="hl"><td class="title">个人消费借款 装修新房</td><td><div class="badges"><span class="badge">B</span><span class="badge">保</span><span class="badge b">新</span></div></td><td>14.52%</td><td>12,782.0 元</td><td>9 个月</td><td><div class="bar"><i><b style="width:61%"></b></i>61.25%</div></td><td><span class="pill">投标</span></td></tr>
      <tr><td class="title">经营周转借款 用于扩大门店规模经营</td><td><div class="badges"><span class="badge">A</span><span class="badge">保</span></div></td><td>15.0%</td><td>50,000 元</td><td>12 个月</td><td><div class="bar"><i><b style="width:100%"></b></i>100.0%</div></td><td><span class="pill off">已满标</span></td></tr>
      <tr><td class="title">车辆抵押借款 短期资金周转</td><td><div class="badges"><span class="badge">A</span><span class="badge">保</span></div></td><td>15.0%</td><td>40,000 元</td><td>12 个月</td><td><div class="bar"><i><b style="width:100%"></b></i>100.0%</div></td><td><span class="pill off">已满标</span></td></tr>
      <tr><td class="title">创业借款 开设新店</td><td><div class="badges"><span class="badge">A</span><span class="badge">保</span></div></td><td>15.0%</td><td>50,000 元</td><td>12 个月</td><td><div class="bar"><i><b style="width:100%"></b></i>100.0%</div></td><td><span class="pill off">已满标</span></td></tr>
    </table>
  </div>
</section>

<section class="stats">
  <div class="wrap">
    <div class="stat"><b>¥ 160407</b><span>平台累计成交 投资人收益</span></div>
    <div class="stat"><b>14.69%</b><span>平均年化收益 稳定可靠</span></div>
    <div class="stat last"><b>12.24 万元已收益</b><span>投资人 累计获得收益 资金安全 透明</span></div>
    <a class="btn-green" href="#">立即投资 <svg viewBox="0 0 14 14"><path d="M2 3h6V0l6 7-6 7v-3H2z" fill="#fff"/></svg></a>
  </div>
</section>

<section class="wrap">
  <h2 class="section-title">投资产品</h2>
  <div class="products">
    <div class="product orange"><div class="k">三个月期理财</div><div class="rate">10.0%</div><div class="d">预期年化收益 代偿保障</div><a class="btn-green" href="#">立即投</a></div>
    <div class="product yellow"><div class="k">六个月期理财</div><div class="rate">11.0%</div><div class="d">预期年化收益 代偿保障</div><a class="btn-green" href="#">立即投</a></div>
    <div class="product red"><div class="k">九个月期理财</div><div class="rate">12.0%</div><div class="d">预期年化收益 代偿保障</div><a class="btn-green" href="#">立即投</a></div>
    <div class="product purple"><div class="k">十二个月期理财</div><div class="rate">13.0%</div><div class="d">预期年化收益 代偿保障</div><a class="btn-green" href="#">立即投</a></div>
  </div>
</section>

<section class="partners wrap">
  <h2>合作银行与机构 共同守护资金</h2>
  <svg class="arr" style="left:0" viewBox="0 0 16 28"><path d="M14 2 3 14l11 12" stroke="#bbb" stroke-width="3" fill="none"/></svg>
  <svg class="arr" style="right:0" viewBox="0 0 16 28"><path d="M2 2l11 12L2 26" stroke="#bbb" stroke-width="3" fill="none"/></svg>
  <div class="banks">
    <span class="bank gr"><i></i>禾丰银行</span>
    <span class="bank"><i></i>华昌银行</span>
    <span class="bank bl"><i></i>建远银行</span>
    <span class="bank bl"><i></i>甬川银行</span>
    <span class="bank"><i></i>广润银行</span>
    <span class="bank"><i></i>工信银行</span>
    <span class="bank"><i></i>中泰银行</span>
    <span class="bank"><i></i>招远银行</span>
    <span class="bank bl"><i></i>夏元银行</span>
    <span class="bank bl"><i></i>通达银行</span>
    <span class="bank gr"><i></i>民安银行</span>
    <span class="bank"><i></i>京华银行</span>
  </div>
</section>

<section class="allies">
  <div class="wrap">
    <span class="ally r"><i></i>Lumora Direct</span>
    <span class="ally"><i></i>小微金融协作会</span>
    <span class="ally"><i></i>Cirrofield</span>
    <span class="ally"><i></i>安信合</span>
    <span class="ally"><i></i>申信征信服务</span>
  </div>
</section>

<footer class="footer">
  <div class="wrap">
    <div class="links">
      <a>关于我们</a><a>新手指引</a>
      <a>公司简介</a><a>帮助</a>
      <a>团队介绍</a><a>资费</a>
      <a>招贤纳士</a><a>安全保障</a>
      <a>联系我们</a><a>媒体报道</a>
    </div>
    <div class="links r">
      <a>我要投资理财 借贷流程</a>
      <a>我要借款融资</a>
      <a>安全保障中心</a>
      <a>新手专享理财活动</a>
      <a>网站地图 帮助中心</a>
    </div>
    <div class="certs"><i></i><i></i><i></i><i></i><i></i><i></i></div>
    <div class="contact">
      <div class="social"><i></i><i></i><i></i><i></i></div>
      <div class="t">关注我们 · 微信客服热线</div>
      <div class="ph">400 - 820 - 5577</div>
      <div class="s">工作日 9:00-18:00 在线客服<br>客服邮箱 · 投诉建议</div>
    </div>
  </div>
  <div class="bottom"><div class="wrap">© 2014 Kelumo.cn 版权所有 · 网络借贷信息服务平台</div></div>
</footer>

</body>
</html>
```